Graphic Design of Business Process

We require an eye-catching, sophisticated design of 2 business processes (attached), that will be used digitally AND for print (to be put on walls in our office).

The basic layout is attached. We require a creative, professional designer to re-design these so that they look appealing but still able to grasp all the information.

We will require vector files and editable project files for final delivery. You may refer to our website (quillharbourworks.com.au) for an indication of our brand.

If you have any questions, please ask.

Thank you.

```html
<!DOCTYPE html>
<html lang="en">
<head>
<meta charset="utf-8">
<title>Content Hierarchy</title>
<link rel="stylesheet" href="https://fonts.googleapis.com/css2?family=Montserrat:wght@700;800&family=Oswald:wght@500;600&display=swap">
<style>
  :root {
    --sky: #a9dcf5;
    --sky-light: #eaf6fd;
    --ink: #0d0d0d;
    --gold: #f7b83f;
    --hero: #4557a7;
    --hero-ring: #5467b5;
    --hero-dark: #2f4699;
    --hub: #b5489b;
    --hub-ring: #c055a6;
    --hub-dark: #7b2470;
    --hygiene: #f7941d;
    --hygiene-ring: #fbb03b;
    --hygiene-light: #ffbe40;
    --pink: #ec1e79;
    --card: #f5f6f6;
    --card-shade: #e6e7e8;
  }
  html, body { margin: 0; padding: 0; overflow: hidden; }
  body { width: 1200px; height: 1051px; }
  .canvas {
    position: relative;
    width: 1200px;
    height: 1051px;
    overflow: hidden;
    background: radial-gradient(ellipse 70% 65% at 50% 48%, #ffffff 0%, var(--sky-light) 55%, var(--sky) 100%);
  }
  .canvas svg { position: absolute; inset: 0; display: block; }
  .title { font-family: "Montserrat", sans-serif; font-weight: 800; font-size: 59px; fill: var(--ink); }
  .tier-name, .tier-desc { font-family: "Oswald", sans-serif; font-weight: 600; text-anchor: middle; }
  .tier-name { font-size: 48px; }
  .tier-desc { font-size: 48px; }
  .hero { fill: var(--hero); }
  .hub { fill: var(--hub); }
  .hygiene { fill: var(--hygiene); }
  .brand { font-family: "Montserrat", sans-serif; font-weight: 800; font-size: 24px; letter-spacing: 5px; fill: var(--ink); text-anchor: middle; }
</style>
</head>
<body>
<main class="canvas">
  <svg width="1200" height="1051" viewBox="0 0 1200 1051" xmlns="http://www.w3.org/2000/svg">
    <defs>
      <linearGradient id="title-panel" x1="0" y1="0" x2="0" y2="1">
        <stop offset="0" stop-color="#f7fcff"/>
        <stop offset="1" stop-color="#d3ecfa"/>
      </linearGradient>
    </defs>

    <!-- Title panel -->
    <path class="title-panel" d="M190 0 H1010 V168 Q1010 228 950 228 H250 Q190 228 190 168 Z" fill="url(#title-panel)"/>
    <text class="title" x="600" y="172" text-anchor="middle">CONTENT HIERARCHY</text>
    <rect class="title-rule" x="242" y="188" width="716" height="9" fill="var(--gold)"/>

    <!-- Cards -->
    <g class="cards">
      <rect x="95" y="480" width="310" height="446" fill="var(--card)"/>
      <rect x="445" y="480" width="310" height="446" fill="var(--card)"/>
      <rect x="795" y="480" width="310" height="446" fill="var(--card)"/>
      <polygon points="250,585 405,495 405,690" fill="var(--card-shade)"/>
      <polygon points="600,585 755,495 755,690" fill="var(--card-shade)"/>
      <polygon points="950,585 1105,495 1105,690" fill="var(--card-shade)"/>
      <polygon points="95,848 95,926 177,926" fill="var(--hero)"/>
      <polygon points="445,848 445,926 527,926" fill="var(--hub)"/>
      <polygon points="795,848 795,926 877,926" fill="var(--hygiene)"/>
    </g>

    <!-- Connecting band -->
    <g class="band">
      <polygon points="75,402 130,372 130,515 75,486" fill="var(--hero-dark)"/>
      <rect x="130" y="372" width="350" height="143" fill="var(--hero-dark)"/>
      <rect x="600" y="372" width="350" height="143" fill="var(--hub-dark)"/>
      <polygon points="1070,372 1125,402 1125,486 1070,515" fill="var(--hygiene-light)"/>
      <rect x="950" y="372" width="120" height="143" fill="var(--hygiene-light)"/>
    </g>

    <!-- Chevron links -->
    <g class="links" stroke-width="5" fill="none">
      <polyline points="305,310 425,385" stroke="var(--hub)"/>
      <polyline points="425,385 545,310" stroke="var(--hero)"/>
      <polyline points="305,580 425,507" stroke="var(--hub)"/>
      <polyline points="425,507 545,580" stroke="var(--hero)"/>
      <polyline points="655,310 775,385" stroke="var(--pink)"/>
      <polyline points="775,385 895,310" stroke="var(--hub)"/>
      <polyline points="655,580 775,507" stroke="var(--pink)"/>
      <polyline points="775,507 895,580" stroke="var(--hub)"/>
    </g>

    <!-- Hexagon badges -->
    <g class="badge">
      <polygon points="250,295 376,368 376,513 250,586 124,513 124,368" fill="var(--hero-ring)"/>
      <polygon points="250,315 359,378 359,503 250,566 141,503 141,378" fill="#3f4f8f"/>
      <polygon points="250,333 343,387 343,494 250,548 157,494 157,387" fill="#ffffff"/>
      <text class="tier-name hero" x="250" y="455">HERO</text>
    </g>
    <g class="badge">
      <polygon points="600,295 726,368 726,513 600,586 474,513 474,368" fill="var(--hub-ring)"/>
      <polygon points="600,315 709,378 709,503 600,566 491,503 491,378" fill="#8e3c7e"/>
      <polygon points="600,333 693,387 693,494 600,548 507,494 507,387" fill="#ffffff"/>
      <text class="tier-name hub" x="600" y="455">HUB</text>
    </g>
    <g class="badge">
      <polygon points="950,295 1076,368 1076,513 950,586 824,513 824,368" fill="var(--hygiene-ring)"/>
      <polygon points="950,315 1059,378 1059,503 950,566 841,503 841,378" fill="#b88a45"/>
      <polygon points="950,333 1043,387 1043,494 950,548 857,494 857,387" fill="#ffffff"/>
      <text class="tier-name hygiene" x="950" y="455">HYGIENE</text>
    </g>

    <!-- Descriptions -->
    <text class="tier-desc hero" x="250" y="706">TENTPOLE</text>
    <text class="tier-desc hero" x="250" y="768">CAMPAIGNS</text>

    <text class="tier-desc hub" x="600" y="706">REGULAR</text>
    <text class="tier-desc hub" x="600" y="768">“PUSH”</text>
    <text class="tier-desc hub" x="600" y="830">CONTENT</text>

    <text class="tier-desc hygiene" x="950" y="706">ALWAYS-ON</text>
    <text class="tier-desc hygiene" x="950" y="768">“PULL”</text>
    <text class="tier-desc hygiene" x="950" y="830">CONTENT</text>

    <!-- Brand name -->
    <text class="brand" x="600" y="996">QUILL HARBOUR WORKS</text>
  </svg>
</main>
</body>
</html>
```